Business Card Design for Marketing Firm

Looking for business card design for higher end marketing firm. Clean but impressionable/trendy. We are a marketing firm that represents manufacturers in the foodservice equipment and supply industry. Our customers are end users such has hotels, restaurants, country clubs, convention centers and casinos as well as distributors of restaurants supplies and equipment, and manufacturers of foodservice equipment and supplies.
Target Market(s)
Hotels, Restaurants, Supply & Equipment Distributors, Foodservice Manufacturers
Industry/Entity Type
Foodservice/Hospitality
Contact Information for Business Card
Name, Title, Contact Number, Email, Website, Social Media, Address
Requirements
Must have
- Clean & Simple but Serious and Impressionable

```html
<!DOCTYPE html>
<html lang="en">
<head>
<meta charset="utf-8">
<title>Meridian Hospitality Reps – Business Card</title>
<link rel="stylesheet" href="https://fonts.googleapis.com/css2?family=Montserrat:wght@400;500;600;700&display=swap">
<style>
  :root {
    --navy: #2b2a78;
    --paper: #ffffff;
    --stage: #9a9a9a;
    --ink: #1f1f2e;
  }
  * { margin: 0; padding: 0; box-sizing: border-box; }
  html, body { width: 1200px; height: 856px; overflow: hidden; }
  body {
    background: var(--stage);
    font-family: "Montserrat", sans-serif;
    position: relative;
  }
  .card {
    position: absolute;
    width: 660px;
    height: 378px;
    box-shadow: 0 10px 28px rgba(0,0,0,.35);
  }
  /* Front */
  .card-front { left: 60px; top: 40px; background: var(--paper); }
  .front-brand {
    position: absolute; left: 34px; top: 120px; width: 300px;
    display: flex; align-items: center; gap: 12px;
  }
  .brand-dot {
    width: 34px; height: 34px; border-radius: 50%;
    background: var(--navy); flex: none;
  }
  .brand-name {
    color: var(--navy); font-weight: 600; font-size: 21px;
    letter-spacing: .04em; line-height: 1.2; text-transform: uppercase;
  }
  .divider {
    position: absolute; left: 354px; top: 42px; width: 1.5px; height: 210px;
    background: var(--navy);
  }
  .contact { position: absolute; left: 378px; top: 42px; color: var(--ink); }
  .contact-name {
    color: var(--navy); font-weight: 700; font-size: 19px; letter-spacing: .02em;
  }
  .contact-title { font-size: 13px; margin: 2px 0 8px; }
  .contact-address { font-size: 13px; line-height: 1.35; margin-bottom: 8px; }
  .contact-list { list-style: none; font-size: 13px; }
  .contact-list li { display: flex; align-items: center; gap: 8px; line-height: 1.55; }
  .contact-list svg { width: 13px; height: 13px; fill: var(--navy); flex: none; }
  .social-dots { display: flex; gap: 3px; }
  .social-dots span {
    width: 12px; height: 12px; border-radius: 50%; background: var(--navy);
  }
  .tagline-band {
    position: absolute; left: 0; right: 0; top: 296px; height: 40px;
    background: var(--navy); color: var(--paper);
    font-size: 13.5px; font-weight: 500; letter-spacing: .02em;
    display: flex; align-items: center; justify-content: center;
  }
  /* Back */
  .card-back {
    left: 480px; top: 438px; background: var(--navy);
    display: flex; align-items: center; justify-content: center; gap: 18px;
  }
  .card-back .brand-dot { width: 52px; height: 52px; background: var(--paper); }
  .card-back .brand-name { color: var(--paper); font-size: 30px; }
</style>
</head>
<body>
  <section class="card card-front" aria-label="Business card front">
    <div class="front-brand">
      <span class="brand-dot"></span>
      <span class="brand-name">Meridian Hospitality Reps</span>
    </div>
    <div class="divider"></div>
    <div class="contact">
      <p class="contact-name">DANIEL HARLOW</p>
      <p class="contact-title">Co-Founder</p>
      <p class="contact-address">P.O. BOX 40-12 LNR-55<br>Linden Ave 9, Fairview</p>
      <ul class="contact-list">
        <li><svg viewBox="0 0 24 24"><path d="M6.6 10.8a15 15 0 0 0 6.6 6.6l2.2-2.2c.3-.3.7-.4 1-.2 1.1.4 2.3.6 3.6.6.6 0 1 .4 1 1V20c0 .6-.4 1-1 1A17 17 0 0 1 3 4c0-.6.4-1 1-1h3.5c.6 0 1 .4 1 1 0 1.3.2 2.5.6 3.6.1.3 0 .7-.2 1z"/></svg>555-014-2290</li>
        <li><svg viewBox="0 0 24 24"><path d="M2 5h20v14H2zm2 2v.5l8 5 8-5V7l-8 5z"/></svg>info@meridianhospitality.com</li>
        <li><svg viewBox="0 0 24 24"><circle cx="12" cy="12" r="10"/></svg>www.meridianhospitality.com</li>
        <li><span class="social-dots"><span></span><span></span><span></span><span></span></span>@meridianhospitality</li>
      </ul>
    </div>
    <div class="tagline-band">Hotels, Restaurants, Supply &amp; Equipment Distributors, Foodservice Manufacturers</div>
  </section>

  <section class="card card-back" aria-label="Business card back">
    <span class="brand-dot"></span>
    <span class="brand-name">Meridian Hospitality Reps</span>
  </section>
</body>
</html>
```